LANTERN - and the quiet crafts of everyday life

I´m writing a book about CHANGE and the skills leaders needs to embody the transformation from being amanager to become leaders.
The title of the book in Icelandic is the same as the name of the project (which I want to be used on the designes is:) UPPSPRETTA
(with the subtitle:) og hugrekki hversdagsins

Change is not controlled or managed – Leading effective change is an art form which is one of the big reasons for why 70% of changes within companies fail. The main reason however, is that managers are tasked with managing and directing them. The art form of change is to put it in the hands of leaders who possess the emotional intelligence that is needed – all their other advantages intact – to lead change all the way.

The big problem when it comes to change is that there are too many managers and too few leaders within companies – leaders who possess emotional intelligence which is the most important skill a leader embodies to empower change. A leader has what it takes to empower followership.

A manager tends to push and control, make decisions that he presupposes others to implement the way he expects. An emotionally competent leader leads by example and enhances followership on that journey because of the trust and respect he has earned.

In few words: SOFT SKILLS ARE THE NEW HARD SKILLS!

```html
<!DOCTYPE html>
<html lang="is">
<head>
<meta charset="utf-8">
<title>Uppspretta – book cover spread</title>
<link rel="stylesheet" href="https://fonts.googleapis.com/css2?family=Libre+Franklin:wght@400;500;800&family=Arimo:wght@400&family=Roboto:ital,wght@0,400;1,400&display=swap">
<style>
  :root {
    --page: #ffffff;
    --ink-black: #0a0a0a;
    --spine-black: #0d0d0d;
    --title-red: #e03a2e;
    --paper-white: #ffffff;
    --body-grey: #e8e8e8;
    --sky-pale: #fdf3c4;
    --sky-gold: #f4c466;
    --sun-orange: #e27a2c;
    --rock-red: #8a2a12;
    --rock-dark: #2a0b05;
  }
  * { margin: 0; padding: 0; box-sizing: border-box; }
  html, body {
    width: 1200px; height: 1200px; overflow: hidden;
    background: var(--page);
  }
  .canvas { position: relative; width: 1200px; height: 1200px; }
  .spread {
    position: absolute; left: 44px; top: 337px;
    width: 1113px; height: 526px; display: flex;
  }

  /* Back cover */
  .back-cover {
    position: relative; width: 525px; height: 100%;
    background: var(--ink-black); color: var(--paper-white);
  }
  .back-title {
    position: absolute; top: 34px; left: 0; width: 100%;
    text-align: center; color: var(--title-red);
    font: 800 51px/1 "Libre Franklin", sans-serif; letter-spacing: 0.5px;
  }
  .back-subtitle {
    position: absolute; top: 90px; left: 0; width: 100%;
    text-align: center; font: 400 18px/1.2 "Roboto", sans-serif;
  }
  .back-subtitle-rule {
    position: absolute; top: 113px; left: 160px; width: 205px; height: 1px;
    background: linear-gradient(90deg, transparent, #bbbbbb, transparent);
  }
  .blurb {
    position: absolute; top: 131px; left: 57px; width: 411px;
    font: 400 9.6px/12.6px "Arimo", sans-serif; color: var(--body-grey);
    text-align: justify;
  }
  .blurb-divider {
    position: absolute; top: 313px; left: 160px; width: 205px; height: 1px;
    background: linear-gradient(90deg, transparent, var(--title-red), transparent);
  }
  .author-photo {
    position: absolute; top: 332px; left: 55px; width: 75px; height: 86px;
    background: var(--paper-white);
  }
  .author-name-back {
    position: absolute; top: 333px; left: 144px;
    font: 500 16px/1 "Libre Franklin", sans-serif;
  }
  .author-bio {
    position: absolute; top: 353px; left: 145px; width: 323px;
    font: 400 9.6px/12.6px "Arimo", sans-serif; color: var(--body-grey);
    text-align: justify;
  }
  .isbn-panel {
    position: absolute; top: 432px; left: 352px; width: 116px; height: 76px;
    background: var(--paper-white);
  }

  /* Spine */
  .spine {
    position: relative; width: 64px; height: 100%;
    background: var(--spine-black);
    border-left: 1px solid #222;
  }
  .spine-title, .spine-author {
    position: absolute; left: 50%; transform: translateX(-50%);
    writing-mode: vertical-rl; white-space: nowrap;
  }
  .spine-title {
    top: 38px; color: var(--title-red);
    font: 800 27px/1 "Libre Franklin", sans-serif; letter-spacing: 1px;
  }
  .spine-author {
    top: 344px; color: var(--paper-white);
    font: 500 14px/1 "Libre Franklin", sans-serif; letter-spacing: 1px;
  }

  /* Front cover */
  .front-cover { position: relative; width: 524px; height: 100%; overflow: hidden; }
  .cover-photo {
    position: absolute; inset: 0;
    background:
      radial-gradient(ellipse 60% 35% at 50% 38%, rgba(255,220,140,0.7), transparent 70%),
      linear-gradient(180deg, var(--sky-pale) 0%, var(--sky-gold) 30%, var(--sun-orange) 52%, var(--rock-red) 72%, var(--rock-dark) 100%);
  }
  .front-title {
    position: absolute; top: 52px; left: 0; width: 100%;
    text-align: center; color: var(--title-red);
    font: 800 67px/1 "Libre Franklin", sans-serif; letter-spacing: 0.5px;
  }
  .front-subtitle {
    position: absolute; top: 130px; left: 0; width: 100%;
    text-align: center; color: #1a1a1a;
    font: italic 400 24px/1.2 "Roboto", sans-serif;
  }
  .author-name-front {
    position: absolute; top: 457px; left: 381px; color: var(--paper-white);
    font: 500 20px/1.2 "Libre Franklin", sans-serif; letter-spacing: 1.5px;
  }
</style>
</head>
<body>
<div class="canvas">
  <div class="spread">
    <section class="back-cover">
      <h2 class="back-title">UPPSPRETTA</h2>
      <p class="back-subtitle">og hugrekki hversdagsins</p>
      <div class="back-subtitle-rule"></div>
      <p class="blurb">Lorem ipsum dolor sit amet, consectetuer adipiscing elit, sed diam nonummy nibh euismod tincidunt ut laoreet dolore magna aliquam erat volutpat. Ut wisi enim ad minim veniam, quis nostrud exerci tation ullamcorper suscipit lobortis nisl ut aliquip ex ea commodo consequat. Duis autem vel eum iriure dolor in hendrerit in vulputate velit esse molestie consequat, vel illum dolore eu feugiat nulla facilisis at vero eros et accumsan et iusto odio dignissim qui blandit praesent luptatum zzril delenit augue duis dolore te feugait nulla facilisi.<br>Lorem ipsum dolor sit amet, cons ectetuer adipiscing elit, sed diam nonummy nibh euismod tincidunt ut laoreet dolore magna aliquam erat volutpat. Ut wisi enim ad minim veniam, quis nostrud exerci tation ullamcorper suscipit lobortis nisl ut aliquip ex ea commodo consequat.<br>Lorem ipsum dolor sit amet, consectetuer adipiscing elit, sed diam nonummy nibh euismod tincidunt ut laoreet dolore magna aliquam erat volutpat. Ut wisi enim ad minim veniam, quis nostrud exerci tation ullamcorper suscipit lobortis nisl ut aliquip ex ea commodo consequat. Duis autem vel eum iriure dolor in hendrerit</p>
      <div class="blurb-divider"></div>
      <div class="author-photo"></div>
      <h3 class="author-name-back">HALLDÓR EINARSSON</h3>
      <p class="author-bio">Lorem ipsum dolor sit amet, consectetuer adipiscing elit, sed diam nonummy nibh euismod tincidunt ut laoreet dolore magna aliquam erat volutpat. Ut wisi enim ad minim veniam, quis nostrud exerci tation ullamcorper suscipit lobortis nisl ut aliquip ex ea commodo consequat. Duis autem vel eum iriure dolor in.</p>
      <div class="isbn-panel"></div>
    </section>

    <section class="spine">
      <span class="spine-title">UPPSPRETTA</span>
      <span class="spine-author">HALLDÓR EINARSSON</span>
    </section>

    <section class="front-cover">
      <div class="cover-photo" role="img" aria-label="Photograph of a person leaping between two rock cliffs against a golden sunset over mountains"></div>
      <h1 class="front-title">UPPSPRETTA</h1>
      <p class="front-subtitle">og hugrekki hversdagsins</p>
      <p class="author-name-front">HALLDÓR<br>EINARSSON</p>
    </section>
  </div>
</div>
</body>
</html>
```